Harborline Renewal Business Card Design

Professional and clean design. The design colors should flow with the logo. Two-sided card with the website on the back which is:

www.HarborlineRenewal.example.

"Specializing in Water Damage Restoration"

On the front I need the name, email, phone, and logo.

Name: Darnell Quisby
Email: Darnell@HarborlineRenewal.example
Phone: 555-318-2046 for now

I only have the Preview and Thumbnail right now but should have the source files uploaded within a day or two.

Target Market(s)

Flood victims, home owners with water damage from busted pipes etc...

Industry/Entity Type

Business

Contact Information for Business Card

Name: Darnell Quisby

Font styles to use
Serif
Sans Serif

Requirements
Must have
• Business Card Details Info

```html
<!DOCTYPE html>
<html lang="en">
<head>
<meta charset="utf-8">
<title>Harborline Renewal Business Card</title>
<link rel="stylesheet" href="https://fonts.googleapis.com/css2?family=Cinzel:wght@600&family=Open+Sans:wght@400;700&display=swap">
<style>
  :root {
    --page-bg: #e9e8e5;
    --card-gray: #a7a7a7;
    --card-white: #ffffff;
    --brand-blue: #2ba2dc;
    --brand-blue-deep: #1d8cc9;
    --rule-gray: #b9b9b9;
    --text-white: #ffffff;
  }
  * { box-sizing: border-box; margin: 0; padding: 0; }
  html, body {
    width: 1200px;
    height: 950px;
    overflow: hidden;
    background: var(--page-bg);
  }
  .card {
    position: absolute;
    left: 250px;
    width: 700px;
    height: 400px;
    overflow: hidden;
    box-shadow: 0 6px 18px rgba(0,0,0,0.18);
  }
  .card-back { top: 45px; background: var(--card-gray); }
  .card-front { top: 505px; background: var(--card-white); }

  .brand {
    display: flex;
    align-items: center;
    gap: 14px;
    font-family: "Cinzel", Georgia, serif;
    font-weight: 600;
    letter-spacing: 1px;
  }
  .brand-dot {
    width: 40px;
    height: 40px;
    border-radius: 50%;
    flex: none;
  }

  .card-back .brand {
    position: absolute;
    top: 140px;
    left: 0;
    right: 0;
    justify-content: center;
    color: var(--text-white);
    font-size: 34px;
  }
  .card-back .brand-dot { background: var(--text-white); }
  .tagline {
    position: absolute;
    top: 228px;
    left: 0;
    right: 0;
    text-align: center;
    font-family: "Open Sans", Arial, sans-serif;
    font-size: 17px;
    color: var(--text-white);
  }

  .swoosh { position: absolute; inset: 0; width: 700px; height: 400px; }

  .card-front .brand {
    position: absolute;
    top: 70px;
    right: 38px;
    color: var(--brand-blue);
    font-size: 30px;
  }
  .card-front .brand-dot { background: var(--brand-blue); }

  .contact {
    position: absolute;
    left: 42px;
    top: 250px;
    color: var(--text-white);
    font-family: "Open Sans", Arial, sans-serif;
  }
  .contact-name {
    font-size: 21px;
    font-weight: 700;
    margin-bottom: 14px;
  }
  .contact-list { list-style: none; }
  .contact-list li {
    display: flex;
    align-items: center;
    gap: 10px;
    font-size: 15px;
    line-height: 26px;
  }
  .contact-icon { width: 15px; height: 15px; flex: none; }
</style>
</head>
<body>

<section class="card card-back" aria-label="Card back">
  <div class="brand"><span class="brand-dot"></span><span class="brand-name">Harborline Renewal</span></div>
  <p class="tagline">Specializing in Water Damage Restoration</p>
</section>

<section class="card card-front" aria-label="Card front">
  <svg class="swoosh" viewBox="0 0 700 400" aria-hidden="true">
    <path d="M0,152 C150,132 265,165 385,245 C490,312 600,338 700,332" fill="none" stroke="var(--rule-gray)" stroke-width="5"/>
    <path d="M0,168 C150,150 262,180 380,258 C485,326 600,352 700,348 L700,400 L0,400 Z" fill="var(--brand-blue)"/>
  </svg>

  <div class="brand"><span class="brand-dot"></span><span class="brand-name">Harborline Renewal</span></div>

  <div class="contact">
    <p class="contact-name">Darnell Quisby</p>
    <ul class="contact-list">
      <li>
        <svg class="contact-icon" viewBox="0 0 16 16" aria-hidden="true"><path d="M3.5 1.5l2.5 0.5 1 3-1.6 1.3c0.8 1.7 2.1 3 3.8 3.8L10.5 8.5l3 1 0.5 2.5-1.8 1.8C7.5 13.5 2.5 8.5 1.7 3.3z" fill="var(--text-white)"/></svg>
        <span>555-318-2046 for now</span>
      </li>
      <li>
        <svg class="contact-icon" viewBox="0 0 16 16" aria-hidden="true"><rect x="1" y="3" width="14" height="10" rx="1" fill="var(--text-white)"/><path d="M1.5 3.8L8 9l6.5-5.2" fill="none" stroke="var(--brand-blue)" stroke-width="1.3"/></svg>
        <span>Darnell@HarborlineRenewal.example</span>
      </li>
      <li>
        <svg class="contact-icon" viewBox="0 0 16 16" aria-hidden="true"><circle cx="8" cy="8" r="7" fill="var(--text-white)"/><path d="M1 8h14M8 1c-3 3.5-3 10.5 0 14M8 1c3 3.5 3 10.5 0 14" fill="none" stroke="var(--brand-blue)" stroke-width="1"/></svg>
        <span>www.HarborlineRenewal.example</span>
      </li>
    </ul>
  </div>
</section>

</body>
</html>
```